Need business card with a logo for a hearing aid sales and audiology business. We have two Hearing Instrument Specialists and one Audiologist on staff. Over 25 years in business. Locally owned and operated. Financing available. Most insurances accepted.

Summit Audio Wellness LLC
48730 W Larchmont, Suite 7
Spokane, WA 99281
509-617-2084
www.summitaudiowell.example

Manager
Tobias Kerrell HIS COHC
License #71829046

Target Market(s)

50yr old + people with a hearing loss.

Industry/Entity Type

Business

Contact Information for Business Card

48730 W Larchmont, Suite 7
Spokane, WA 99281
509-617-2084
www.summitaudiowell.example

Manager
Tobias Kerrell HIS COHC
NLVE #71829046

Font styles to use
Serif
Sans Serif

Requirements
Must have
• Business name, Tobias's name and title(s) and contact information, License #, web address

```html
<!DOCTYPE html>
<html lang="en">
<head>
<meta charset="utf-8">
<title>Summit Audio Wellness – Business Card</title>
<link rel="stylesheet" href="https://fonts.googleapis.com/css2?family=Open+Sans:wght@400;600;700&family=Raleway:wght@500;600&display=swap">
<style>
  :root {
    --stage: #000000;
    --front-blue: #0f65a0;
    --back-green: #20620b;
    --ink-light: #ffffff;
  }
  * { margin: 0; padding: 0; box-sizing: border-box; }
  html, body { width: 1200px; height: 900px; overflow: hidden; background: var(--stage); }
  .canvas { position: relative; width: 1200px; height: 900px; background: var(--stage); }

  .card { position: absolute; top: 275px; height: 293px; width: 477px; color: var(--ink-light); }
  .card-front {
    left: 116px; background: var(--front-blue);
    border-radius: 0 62px 0 62px;
    font-family: "Open Sans", Arial, sans-serif;
  }
  .card-back {
    left: 622px; top: 276px; height: 292px; background: var(--back-green);
    border-radius: 62px 0 62px 0;
  }

  .front-brand {
    position: absolute; left: 60px; top: 82px;
    font-family: "Open Sans", Arial, sans-serif; font-weight: 700;
    font-size: 30px; line-height: 1.05; letter-spacing: 0.5px;
  }

  .holder { position: absolute; right: 20px; top: 44px; text-align: right; }
  .holder-name { font-weight: 700; font-size: 15px; line-height: 18px; }
  .holder-name .creds { font-weight: 400; font-size: 12.5px; }
  .holder-role { font-size: 12.5px; line-height: 14px; }

  .license { position: absolute; right: 20px; top: 174px; font-weight: 600; font-size: 12.5px; }

  .contact { position: absolute; right: 20px; top: 206px; text-align: right; font-size: 12.5px; line-height: 17px; }
  .contact-line { display: flex; justify-content: flex-end; align-items: center; gap: 5px; }
  .contact-line svg { width: 10px; height: 10px; fill: var(--ink-light); }
  .address { margin-top: 7px; margin-right: 0; }

  .back-brand {
    position: absolute; left: 0; right: 0; top: 108px; text-align: center;
    font-family: "Raleway", Arial, sans-serif; font-weight: 500;
    font-size: 27px; line-height: 34px; letter-spacing: 0.2px;
  }
</style>
</head>
<body>
<div class="canvas">
  <section class="card card-front">
    <div class="front-brand">Summit<br>Audio<br>Wellness</div>

    <div class="holder">
      <p class="holder-name">Tobias Kerrell <span class="creds">HIS COHC</span></p>
      <p class="holder-role">Manager</p>
    </div>

    <p class="license">License #71829046</p>

    <div class="contact">
      <p class="contact-line">509-617-2084
        <svg viewBox="0 0 24 24" aria-hidden="true"><path d="M6.6 10.8a15.1 15.1 0 0 0 6.6 6.6l2.2-2.2a1 1 0 0 1 1-.25 11.4 11.4 0 0 0 3.6.57 1 1 0 0 1 1 1V20a1 1 0 0 1-1 1A17 17 0 0 1 3 4a1 1 0 0 1 1-1h3.5a1 1 0 0 1 1 1c0 1.25.2 2.45.57 3.57a1 1 0 0 1-.25 1z"/></svg>
      </p>
      <p class="contact-line">www.summitaudiowell.example
        <svg viewBox="0 0 24 24" aria-hidden="true"><path d="M12 2a10 10 0 1 0 0 20 10 10 0 0 0 0-20zm-1 17.9A8 8 0 0 1 4 12c0-.6.1-1.2.2-1.8L9 15v1a2 2 0 0 0 2 2zm6.9-2.5A2 2 0 0 0 16 16h-1v-3a1 1 0 0 0-1-1H8v-2h2a1 1 0 0 0 1-1V7h2a2 2 0 0 0 2-2v-.4a8 8 0 0 1 2.9 12.8z"/></svg>
      </p>
      <p class="address">48730 W Larchmont, Suite 7 Spokane, WA 99281</p>
    </div>
  </section>

  <section class="card card-back">
    <div class="back-brand">Summit Audio Wellness<br>LLC</div>
  </section>
</div>
</body>
</html>
```